Business Card for premium dental clinic

We are a premium dental clinic based in Brasov, Romania with more than 15 year on the market, providing quality dental treatment made by a team of more specialized dentists, working with modern equipment as a solution to beautiful and healthy teeth.

Our current logo for the clinic use 2 square with colors black and gold - dr Ternisu - studio, using family fonts Bodoni, Myriad Pro and Segoe Print.
Depending on the printing we used some gold CMYK background or gold foil picture background or a gold gradient.
We want a business card:
- eye catching business card
- distinguished business card
- premium design
- to keep the color scheme of black and gold
- to attract the customers to spent time reading the information
- modern concept

```html
<!DOCTYPE html>
<html lang="ro">
<head>
<meta charset="utf-8">
<title>Atrium Dental Clinic – Business Card</title>
<link rel="stylesheet" href="https://fonts.googleapis.com/css2?family=Dosis:wght@500;600&display=swap">
<style>
  :root {
    --backdrop: #2b211c;
    --card: #2d2e30;
    --card-shade: #272829;
    --gold: #c9a02e;
    --ink: #121212;
    --gloss-dark: #0b0b0b;
    --gloss-light: #5a5b5e;
  }
  * { margin: 0; padding: 0; box-sizing: border-box; }
  html, body {
    width: 1200px;
    height: 800px;
    overflow: hidden;
    background: var(--backdrop);
  }
  .canvas {
    position: relative;
    width: 1200px;
    height: 800px;
    display: flex;
    align-items: center;
    justify-content: center;
    gap: 48px;
  }
  .card {
    width: 520px;
    height: 336px;
    background: linear-gradient(160deg, var(--card) 0%, var(--card-shade) 100%);
    border: 2px solid var(--gold);
    position: relative;
    display: flex;
    align-items: center;
    justify-content: center;
  }
  .card-front .clinic-name {
    font-family: "Dosis", sans-serif;
    font-weight: 600;
    font-size: 40px;
    letter-spacing: 1px;
    color: var(--ink);
  }
  .card-back .doctor-name {
    font-family: "Dosis", sans-serif;
    font-weight: 500;
    font-size: 84px;
    letter-spacing: 1px;
    line-height: 1;
    background: linear-gradient(100deg, var(--gloss-dark) 0%, var(--gloss-dark) 40%, var(--gloss-light) 100%);
    -webkit-background-clip: text;
    background-clip: text;
    color: transparent;
    transform: translateY(10px);
  }
  .doctor-name .title {
    font-size: 58px;
  }
</style>
</head>
<body>
  <main class="canvas">
    <section class="card card-front">
      <p class="clinic-name">Atrium Dental Clinic</p>
    </section>
    <section class="card card-back">
      <p class="doctor-name"><span class="title">dr.</span> Ternisu</p>
    </section>
  </main>
</body>
</html>
```